K & R Acre Works. Business card design

We need a business card designed for a new business. We have a bulldozer and tractor service. We clear land and make wildlife food plots. We provide disking, bush hogging, and site prep services.
I have attached an image of a business card that I like and would like my business cards to look similar.

Target Market(s)

anyone needing bulldozer and/or tractor services

Industry/Entity Type

Business

Contact Information for Business Card

K & R Acre Works, Operated by 7-T-Ranch
Wade Colton
601-472-3358
wcr4817@fieldmail-example.com

Font styles to use
Sans Serif

Colors

Designer to choose colors to be used in the design.

Requirements
Must have
• image of tractor and bulldozer
• Land Clearing
• Wildlife food plots
• Bush Hogging
• Disking
• Site prep
Nice to have
• i have included a image of a business card that i like. I would like mine to be similar.

```html
<!DOCTYPE html>
<html lang="en">
<head>
<meta charset="utf-8">
<title>K &amp; R Acre Works — Business Card</title>
<link rel="stylesheet" href="https://fonts.googleapis.com/css2?family=Roboto+Condensed:wght@400;700&family=Open+Sans:wght@400;600&display=swap">
<style>
  :root {
    --backdrop: #3a3a3a;
    --card: #f3f3f3;
    --olive: #9c9a37;
    --brown: #6b4413;
    --logo-olive: #8e932f;
    --ink: #2b2b2b;
    --white: #ffffff;
    --photo-dozer-a: #8a8a6a;
    --photo-dozer-b: #6b6048;
    --photo-tractor-a: #7f8a52;
    --photo-tractor-b: #b9a06a;
  }
  * { margin: 0; padding: 0; box-sizing: border-box; }
  html, body { width: 1200px; height: 960px; overflow: hidden; }
  body { background: var(--backdrop); position: relative; }

  .card {
    position: absolute; left: 75px; top: 180px;
    width: 1050px; height: 600px;
    background: var(--card);
    overflow: hidden;
  }
  .brand {
    position: absolute; left: 311px; top: 88px; width: 428px;
    font-family: "Roboto Condensed", sans-serif;
  }
  .brand-name {
    display: flex; align-items: center; gap: 10px;
    font-weight: 700; font-size: 34px; line-height: 1;
    color: var(--logo-olive); letter-spacing: 0.5px;
  }
  .brand-mark { width: 26px; height: 26px; background: var(--brown); }
  .brand-tagline {
    margin-top: 6px;
    font-weight: 700; font-size: 16px; color: var(--ink);
    letter-spacing: 0.2px; white-space: nowrap;
  }
  .photo { position: absolute; top: 170px; height: 138px; }
  .photo-dozer {
    left: 311px; width: 231px;
    background: linear-gradient(160deg, var(--photo-dozer-a), var(--photo-dozer-b));
  }
  .photo-tractor {
    left: 552px; width: 186px;
    background: linear-gradient(160deg, var(--photo-tractor-a), var(--photo-tractor-b));
  }

  .contact-band {
    position: absolute; left: 0; top: 399px; width: 100%; height: 131px;
    background: var(--olive); color: var(--white); text-align: center;
  }
  .contact-name {
    margin-top: 28px;
    font-family: "Roboto Condensed", sans-serif;
    font-weight: 700; font-size: 36px; line-height: 1;
  }
  .contact-role { font-size: 26px; font-weight: 400; }
  .contact-details {
    margin-top: 14px;
    font-family: "Open Sans", sans-serif; font-size: 23px;
  }
  .divider {
    position: absolute; left: 0; top: 530px; width: 100%; height: 4px;
    background: var(--card);
  }
  .services-band {
    position: absolute; left: 0; top: 534px; width: 100%; height: 66px;
    background: var(--brown); color: var(--white);
    display: flex; align-items: center; justify-content: center;
    font-family: "Open Sans", sans-serif; font-size: 24px;
  }
</style>
</head>
<body>
  <div class="card">
    <div class="brand">
      <div class="brand-name"><span class="brand-mark"></span>K &amp; R ACRE WORKS</div>
      <div class="brand-tagline">FOR ALL OF YOUR LAND IMPROVEMENT NEEDS</div>
    </div>
    <div class="photo photo-dozer" role="img" aria-label="Photo of a yellow bulldozer pushing soil on a cleared lot"></div>
    <div class="photo photo-tractor" role="img" aria-label="Photo of an orange tractor with front loader in a grassy field"></div>

    <div class="contact-band">
      <div class="contact-name">WADE COLTON - <span class="contact-role">OWNER</span></div>
      <div class="contact-details">P. 601-472-3358 E. wcr4817@fieldmail-example.com W. kracreworks-example.com</div>
    </div>
    <div class="divider"></div>
    <div class="services-band">Land Clearing | Wildlife food plots | Bush Hogging | Disking | Site prep</div>
  </div>
</body>
</html>
```